Redesign of agriculture and industrial webshop.

We are a chemical company that develops and produces all kinds of liquids. Cleaning products but also agriculture health products are our specialty. For both of them we have seperate webshops. www.brimfeldchemics.com/agriculture and www.brimfeldchemics.com/industrials. Both working with wordpress and visual composer to create the content. We'd like a modern and new professional redesign of the webshop to optimize sales and generating new clients. We have just redesigned our main page www.brimfeldchemics.com, this is not a webshop so it has different functions. But we'd like to take the choice of color to match the webshop colors. If you need any source documents, please let me know.

Target Market(s)

Agriculture market in the Netherlands and Industrials cleaning, lubrication market in The Netherlands

Industry/Entity Type

Agriculture

Number of Pages Required

2 page

Requirements
Must have
• Marketing strategies, colors, market segment, webshop look, webshop optimization for sales.
• Please design a homepages, product page, contact page and about us page for both webshops.

```html
<!DOCTYPE html>
<html lang="en">
<head>
<meta charset="utf-8">
<title>Brimfeld – Shopping Basket</title>
<link rel="stylesheet" href="https://fonts.googleapis.com/css2?family=PT+Sans:wght@400;700&family=Roboto:wght@400;500&family=Lato:wght@400;700&display=swap">
<style>
:root{
  --orange:#f26b0a;
  --orange-dark:#e2560a;
  --green:#8dc63f;
  --green-dark:#5e9c2b;
  --green-text:#5ea12a;
  --grey-bg:#f1f1f1;
  --grey-btn:#a8a8a8;
  --label-bg:#e4e4e4;
  --ink:#222;
  --muted:#555;
  --white:#fff;
}
*{box-sizing:border-box;margin:0;padding:0}
html,body{width:897px;height:1200px;overflow:hidden;background:var(--white)}
body{position:relative;font-family:"PT Sans",sans-serif;color:var(--ink)}
.abs{position:absolute}

/* top bar */
.topbar{left:0;top:0;width:897px;height:30px;background:#f7f7f7;border-bottom:1px solid #bbb;font-family:"Roboto",sans-serif;font-size:10px}
.lang{left:134px;top:0;width:64px;height:30px;background:#e6e6e6;display:flex;align-items:center;justify-content:center;gap:4px;color:#333}
.flag{width:15px;height:9px;background:#2c3f8a}
.callus{left:240px;top:9px;color:#222;display:flex;gap:3px;align-items:center}
.callus span{color:var(--green-dark)}
.account-links{right:137px;top:10px;color:#222;font-size:9.5px}

/* header */
.brand{left:136px;top:50px;font-family:"PT Sans",sans-serif;font-weight:700;font-size:32px;color:var(--orange);letter-spacing:-0.5px;line-height:34px}
.search{left:336px;top:58px;width:243px;height:25px;border:1px solid #999;background:#f7f7f7;display:flex;align-items:center;padding-left:10px;gap:6px;font-family:"Roboto",sans-serif;font-size:10px;color:#666}
.cart{left:671px;top:59px;display:flex;align-items:center;gap:6px;font-family:"Roboto",sans-serif;font-size:12px;color:#333}

/* nav */
.mainnav{left:0;top:107px;width:897px;height:33px;background:var(--green)}
.mainnav a{position:absolute;top:10px;color:var(--white);font-family:"Roboto",sans-serif;font-weight:500;font-size:10px;text-decoration:none}

/* basket */
.page-title{left:136px;top:170px;font-size:29px;font-weight:400;letter-spacing:0.5px}
.basket{left:136px;top:232px;width:626px;height:203px;border:1px solid #ccc;border-top:none}
.basket-head{position:absolute;left:0;top:0;width:626px;height:38px;background:var(--orange);border-bottom:2px solid #d85a05;color:var(--white);font-size:13.5px;font-weight:700}
.basket-head div{position:absolute;top:12px}
.col-line{position:absolute;top:0;width:1px;height:202px;background:#ccc}
.product-shot{left:52px;top:52px;width:44px;height:120px;border-radius:6px 6px 8px 8px;background:linear-gradient(#e9b8c0 0 70%,#6fb24a 70% 100%)}
.product-name{left:121px;top:102px;font-size:13px;color:#555;letter-spacing:.3px}
.product-size{left:121px;top:120px;font-size:19px;color:#222}
.price{left:268px;top:100px;font-size:16px;color:#555}
.qty{left:370px;top:92px;width:85px;height:37px;border:1px solid #ccc;background:var(--white)}
.qty span{position:absolute;left:14px;top:9px;font-size:16px;color:#444}
.qty .step{position:absolute;right:0;top:0;width:26px;height:35px;background:#eee;border-left:1px solid #ccc;color:var(--orange);font-size:12px;text-align:center;line-height:14px;padding-top:3px}
.line-total{left:517px;top:97px;font-size:20px;color:var(--green-text)}

.btn{border-radius:30px;color:var(--white);font-weight:700;display:flex;align-items:center;justify-content:center;letter-spacing:.3px}
.btn-grey{background:var(--grey-btn)}
.btn-green{background:var(--green-dark)}
.btn-lg{height:46px;width:208px;font-size:12px}
.btn-sm{height:33px;width:151px;font-size:8.5px;font-family:"Roboto",sans-serif}

/* grey section */
.hills{left:88px;top:572px;width:728px;height:54px;background:linear-gradient(to top,#ececec,rgba(236,236,236,0))}
.grey-zone{left:0;top:624px;width:897px;height:338px;background:var(--grey-bg)}
.section-title{font-size:22px;font-weight:400;letter-spacing:.3px}
.field{height:39px;display:flex;background:var(--white);font-size:12px}
.field .label{width:109px;background:var(--label-bg);display:flex;align-items:center;justify-content:center;color:#333}
.field .value{padding-left:20px;display:flex;align-items:center;color:#222}
.btn-black{left:141px;top:821px;width:161px;height:38px;background:#000;border-radius:20px;color:var(--white);font-size:13px;display:flex;align-items:center;justify-content:center}

.totals{left:498px;top:707px;width:296px;border:1px solid #ddd;background:var(--white)}
.totals .row{height:33px;border-bottom:1px solid #ddd;position:relative;font-size:13px}
.totals .row:last-child{border-bottom:none;background:var(--orange);color:var(--white)}
.totals .k{position:absolute;left:15px;top:9px}
.totals .v{position:absolute;left:158px;top:7px;font-size:11px;font-weight:700;color:var(--green-text)}
.totals .row:last-child .v{color:var(--white)}

/* footer */
.footer{left:0;top:962px;width:897px;height:238px;background:linear-gradient(#f7801e,#f66a10 60%,#f05f0c)}
.footer-base{left:0;top:1156px;width:897px;height:44px;background:var(--orange-dark);color:#fde;font-family:"Lato",sans-serif;font-size:8.5px;text-align:center;padding-top:13px}
.fcol{top:1004px;font-family:"Lato",sans-serif;color:var(--white)}
.fcol h4{font-size:10.5px;font-weight:700;margin-bottom:10px}
.fcol li{list-style:none;font-size:9.5px;margin-bottom:7px;color:#fff3e8}
.news-text{font-size:9.5px;margin-bottom:10px}
.news-input{width:169px;height:27px;border:2px solid #f9b98c;font-size:8px;color:#fff;padding:8px 10px}
.subscribe{margin-top:9px;width:89px;height:23px;background:var(--green-dark);font-size:9.5px;font-weight:700;display:flex;align-items:center;justify-content:center}
.social{display:flex;gap:5px}
.social i{width:23px;height:23px;border:1.5px solid #fff;border-radius:50%;display:block}
.cards{display:flex;gap:6px;margin-top:12px}
.cards i{width:21px;height:13px;background:#fff;border-radius:2px;display:block;opacity:.9}
</style>
</head>
<body>

<header>
  <div class="abs topbar">
    <div class="abs lang"><span class="flag"></span>ENG
      <svg width="8" height="5" viewBox="0 0 8 5"><path d="M0 0l4 4 4-4" fill="none" stroke="#333"/></svg></div>
    <div class="abs callus">
      <svg width="11" height="11" viewBox="0 0 24 24"><path d="M6.6 10.8a15 15 0 0 0 6.6 6.6l2.2-2.2c.3-.3.7-.4 1-.2 1.1.4 2.3.6 3.6.6.6 0 1 .4 1 1V20c0 .6-.4 1-1 1A17 17 0 0 1 3 4c0-.6.4-1 1-1h3.5c.6 0 1 .4 1 1 0 1.3.2 2.5.6 3.6.1.3 0 .7-.2 1z" fill="#444"/></svg>
      CALL US <span>+31 412 66 20 17</span></div>
    <div class="abs account-links">My Account &nbsp;|&nbsp; Wishlist &nbsp;|&nbsp; Login &nbsp;|&nbsp; Checkout</div>
  </div>

  <div class="abs brand">BRIMFELD</div>
  <div class="abs search">
    <svg width="12" height="12" viewBox="0 0 12 12"><circle cx="5" cy="5" r="3.8" fill="none" stroke="#666" stroke-width="1.4"/><path d="M8 8l3 3" stroke="#666" stroke-width="1.6"/></svg>
    Search here...
  </div>
  <div class="abs cart">
    <svg width="26" height="22" viewBox="0 0 26 22"><path d="M7 8a6 6 0 0 1 12 0" fill="none" stroke="#f26b0a" stroke-width="2"/><path d="M1 8h24l-3 13H4z" fill="#f26b0a"/><path d="M8 11v7M13 11v7M18 11v7" stroke="#fff" stroke-width="1.5"/></svg>
    0 ITEMS
  </div>

  <nav class="abs mainnav">
    <a style="left:158px">HOME</a><a style="left:230px">ABOUT US</a><a style="left:301px">CATTLE</a><a style="left:360px">POULTRY</a><a style="left:429px">CROP</a><a style="left:478px">AUXILIARY PRODUCTS</a><a style="left:606px">KNOWLEDGE</a><a style="left:690px">PACKAGING</a>
  </nav>
</header>

<main>
  <h1 class="abs page-title">SHOPPING BASKET</h1>

  <section class="abs basket">
    <div class="basket-head">
      <div style="left:38px">PRODUCT</div><div style="left:269px">PRISE</div><div style="left:370px">QUANTITY</div><div style="left:513px">TOTAL</div>
    </div>
    <div class="col-line" style="left:238px"></div>
    <div class="col-line" style="left:345px"></div>
    <div class="col-line" style="left:489px"></div>
    <div class="abs product-shot" role="img" aria-label="Bottle of Nutra Koe cattle supplement, 10 litre"></div>
    <div class="abs product-name">NUTRA KOE</div>
    <div class="abs product-size">10 LITER</div>
    <div class="abs price">£88,00</div>
    <div class="abs qty"><span>02</span><div class="step">+<br>–</div></div>
    <div class="abs line-total">£176,00</div>
  </section>

  <div class="abs btn btn-grey btn-lg" style="left:240px;top:464px">UPDATE SHOPPING BASKET</div>
  <div class="abs btn btn-green btn-lg" style="left:453px;top:464px">CONTINUE TO CHECKOUT</div>

  <div class="abs hills" role="img" aria-label="Faint landscape silhouette"></div>
  <section class="abs grey-zone"></section>

  <h2 class="abs section-title" style="left:143px;top:662px">CALCULATING SHIPPING COSTS</h2>
  <div class="abs field" style="left:146px;top:715px;width:320px"><div class="label">COUNTRY</div><div class="value">Nederland</div></div>
  <div class="abs field" style="left:145px;top:762px;width:321px"><div class="label">POSTCODE /ZIP</div><div class="value">Postcode /zip</div></div>
  <div class="abs btn-black">TOTAL UPDATE</div>

  <h2 class="abs section-title" style="left:498px;top:662px">TOTAL</h2>
  <div class="abs totals">
    <div class="row"><span class="k">SUBTOTAL</span><span class="v">£176,00</span></div>
    <div class="row"><span class="k">VERZENDING</span><span class="v">Vast Tarief:&nbsp; £9.95</span></div>
    <div class="row"><span class="k">6% BTW</span><span class="v">£10.56</span></div>
    <div class="row"><span class="k">TOTAL</span><span class="v">£196.51</span></div>
  </div>
  <div class="abs btn btn-grey btn-sm" style="left:490px;top:859px">UPDATE SHOPPING BASKET</div>
  <div class="abs btn btn-green btn-sm" style="left:645px;top:859px">CONTINUE TO CHECKOUT</div>
</main>

<footer>
  <div class="abs footer"></div>
  <div class="abs fcol" style="left:136px">
    <h4>SIGN UP NEWSLETTER</h4>
    <p class="news-text">Please sign up for newsletter</p>
    <div class="news-input">Email address</div>
    <div class="subscribe">SUBSCRIBE</div>
  </div>
  <div class="abs fcol" style="left:350px"><h4>COMPANY</h4><ul><li>Home</li><li>About Us</li><li>Our Producs</li><li>Cattle</li></ul></div>
  <div class="abs fcol" style="left:441px"><h4>PRODUCTS</h4><ul><li>Poultry</li><li>Crop</li><li>Auxiliary Prouducts</li><li>Knowledge</li></ul></div>
  <div class="abs fcol" style="left:550px"><h4>RESOURCES</h4><ul><li>My Account</li><li>Cart</li><li>Support</li><li>Contact Us</li></ul></div>
  <div class="abs fcol" style="left:642px"><h4>FOLLOW US</h4>
    <div class="social"><i></i><i></i><i></i><i></i></div>
    <div class="cards"><i></i><i></i><i></i><i></i><i></i></div>
  </div>
  <div class="abs footer-base">© 2018 Company Name&nbsp; All right reserved</div>
</footer>

</body>
</html>
```